Hardcore nerd needs to stand out in a sea of dull Defence business cards

Wombarra Devices is a new Australian consulting engineering company that turns research and theory into practical systems. No evangelistic fluff, just mathematics and physics into electronic and optical circuits for consumer products, scientific research or Defence applications.

We already have a recognised logo (provided) which is often dark blue/black on a light background but we're open to other combinations. (Us engineers tend to have limited aesthetic imagination :)

Some of our recent products have included:
* Instrumentation for electrical testing,
* Radar jammers,
* GPS antenna design,
* Satellite tracking systems,
* High power lasers

We're open to both single and double-sided designs - happy to be convinced either way.

P.S. Another group is working on the web page, so - alas - our web site is currently of no use for images/ideas...

Target Market(s)

Engineering managers,
Scientists

Contact Information for Business Card

Dr Colin Harte
R&D Engineer

colin@wombarradevices.com.au
0427 563 710

PO Box XXX (to be confirmed)
Kelsby ACT 2917
Australia

Font styles to use
Serif
Sans Serif

Colors

Designer to choose colors to be used in the design.

Requirements
Must have
• My contact details!
• I've had many (great) "bold and plain" designs submitted already, so feel free to be artistically creative :)
• Happy to take advice re fonts/colours/printability etc.
Nice to have
• I'm not sure if "lists" are more at home on a CV than a business card, but representative services include:
• Applied electromagnetics
• RF and high speed electronics
• Signal and image processing
• Electro-optical and laser systems
• Concept-to-prototype design services
• If you're considering double sided cards, then often measuring/alignment grids/rulers feature on the back of similar cards.
• e.g. https://www.veltranoptics.example/newgrouppage9.cfm?objectgroup_id=4183
• https://www.veltranoptics.example/newgrouppage9.cfm?objectgroup_ID=4185
• ..or even a "Smith chart" (google will return lots)
• Generic images to represent a capability might work - googling images associated with keyword for each of these areas might help:
• - "passive radar", "phased array", "fdtd", "vircator"
• RF and high speed electronic design
• - "smith chart", "microstrip circuits", "dimensioned drawing", "electronic schematic"
• - "dft", "iir filter"
• - "optical cavity". "laser energy level diagram"
• Background/watermarked images outlines/wireframes/schematics would probably look OK.
Should not have
• If a list of projects/services is provided, it is important not to make the client feel that this is "all" the company can do. Engineering design is a creative discipline (like graphics :)
• Please, no stock "military" snaps like planes, missiles, etc!

```html
<!DOCTYPE html>
<html lang="en">
<head>
<meta charset="utf-8">
<title>Wombarra Devices – Business Card</title>
<link rel="stylesheet" href="https://fonts.googleapis.com/css2?family=Roboto:ital,wght@0,400;0,700;1,300;1,400&display=swap">
<style>
  :root {
    --navy: #0c2a78;
    --navy-deep: #0a2468;
    --pattern-tone: #0d2c80;
    --paper: #ffffff;
    --ink-grey: #5a5a5a;
    --stage: #2b2b2b;
  }
  * { margin: 0; padding: 0; box-sizing: border-box; }
  html, body { width: 1200px; height: 878px; overflow: hidden; }
  body {
    background: var(--stage);
    font-family: "Roboto", sans-serif;
    position: relative;
  }
  .card {
    position: absolute;
    left: 267px;
    width: 665px;
    height: 380px;
    box-shadow: 0 10px 30px rgba(0,0,0,.45);
    overflow: hidden;
  }
  /* Back of card */
  .card-back { top: 34px; background: var(--navy-deep); }
  .card-back .brand-pattern {
    position: absolute; inset: 0;
    background: radial-gradient(circle at 50% 50%, var(--pattern-tone), var(--navy-deep));
  }
  .card-back .brand-name {
    position: absolute;
    right: 70px; top: 150px;
    color: var(--paper);
    font-weight: 700;
    font-size: 18px;
    letter-spacing: 1px;
    text-transform: uppercase;
  }
  /* Front of card */
  .card-front { top: 462px; background: var(--paper); }
  .brand-tab {
    position: absolute; left: 40px; top: 0;
    width: 80px; height: 80px;
    background: var(--navy);
  }
  .brand-wordmark {
    position: absolute; left: 136px; top: 32px;
    color: var(--navy);
    font-weight: 700;
    font-size: 26px;
    letter-spacing: 1.5px;
    text-transform: uppercase;
  }
  .holder-name {
    position: absolute; right: 58px; top: 190px;
    color: var(--navy);
    font-weight: 700; font-size: 27px;
    text-transform: uppercase;
  }
  .holder-role {
    position: absolute; right: 58px; top: 226px;
    color: var(--ink-grey);
    font-size: 15px; letter-spacing: .5px;
  }
  .accent-bar {
    position: absolute; right: 0; top: 198px;
    width: 10px; height: 46px;
    background: var(--navy);
  }
  .divider {
    position: absolute; left: 55px; right: 55px; top: 253px;
    height: 2px; background: var(--navy);
  }
  .contact-list {
    position: absolute; left: 55px; top: 266px;
    list-style: none;
    color: var(--ink-grey);
    font-style: italic; font-weight: 300;
    font-size: 14.5px; letter-spacing: .6px;
  }
  .contact-list li { display: flex; align-items: center; gap: 8px; height: 22px; }
  .contact-list svg { width: 12px; height: 12px; flex: none; }
  .contact-list .web { color: var(--navy); font-weight: 400; }
  .postal-address {
    position: absolute; right: 58px; top: 300px;
    text-align: right;
    color: var(--ink-grey);
    font-size: 15.5px; line-height: 23px; letter-spacing: .6px;
    font-style: normal;
  }
</style>
</head>
<body>

<section class="card card-back">
  <div class="brand-pattern" role="img" aria-label="Faint embossed repeat of the company mark across the navy card"></div>
  <span class="brand-name">Wombarra Devices</span>
</section>

<section class="card card-front">
  <div class="brand-tab"></div>
  <span class="brand-wordmark">Wombarra Devices</span>

  <h1 class="holder-name">Dr Colin Harte</h1>
  <p class="holder-role">R&amp;D Engineer</p>
  <div class="accent-bar"></div>
  <div class="divider"></div>

  <ul class="contact-list">
    <li>
      <svg viewBox="0 0 12 12" aria-hidden="true"><path d="M3 1 L5 3.5 L4 5 Q5 7 7 8 L8.5 7 L11 9 L9.5 11 Q4 10.5 1 3 Z" fill="var(--navy)"/></svg>
      0427 563 710
    </li>
    <li>
      <svg viewBox="0 0 12 12" aria-hidden="true"><rect x="1" y="2.5" width="10" height="7" fill="none" stroke="var(--navy)" stroke-width="1"/><path d="M1 2.5 L6 6.5 L11 2.5" fill="none" stroke="var(--navy)" stroke-width="1"/></svg>
      colin@wombarradevices.com.au
    </li>
    <li>
      <svg viewBox="0 0 12 12" aria-hidden="true"><circle cx="6" cy="6" r="5" fill="none" stroke="var(--navy)" stroke-width="1"/><ellipse cx="6" cy="6" rx="2.2" ry="5" fill="none" stroke="var(--navy)" stroke-width=".8"/><path d="M1 6 H11" stroke="var(--navy)" stroke-width=".8"/></svg>
      <span class="web">www.wombarradevices.com.au</span>
    </li>
  </ul>

  <address class="postal-address">
    PO Box XXX (to be confirmed)<br>
    Kelsby ACT 2917 Australia
  </address>
</section>

</body>
</html>
```